Jamaica's famous and historical Blue Mountian natural spring Quelvane Water

A powerful source of Natural Spring Water coming from Exotic Jamaica's highest and historical Blue Mountains. Springing up cold ,crystal clear, and pristine from Jamaica's natural underground aquifer, percolating from Blue Mountains Peak, the highest in the entire Caribbean. process through a seven stage process , providing the greatest taste and environmentally friendly water source for hydration and nutrition! The bottle is BPA certified and biodegradable and E-friendly. Naturally balance Akalinity and Ph., without all the contaminant and pollutants. The colors need to represent Blue Mountain( rays,colors, and hues)and the exotic mountains of Jamaica and natures natural rays and hues

Target Market(s)

World wide consumers

Requirements
Must have
• Wonderful colors typifying mystical mountains of Blue Moutain Jamician. A highly polished, clean, and professional image to represent the best water in the world!
Nice to have
• Psychologically accepted and marketable colors and hues!
Should not have
• Comical images or suspicions

```html
<!DOCTYPE html>
<html lang="en">
<head>
<meta charset="utf-8">
<title>Quelvane Water – Spring Poster</title>
<link rel="stylesheet" href="https://fonts.googleapis.com/css2?family=Michroma&display=swap">
<style>
  :root {
    --board-black: #000000;
    --frame-blue: #8db6cf;
    --frame-silver: #d9d9d9;
    --poster-grey: #bdbdbd;
    --brand-red: #e41f2b;
    --sun-yellow: #fff27a;
    --sun-orange: #f39a2a;
    --mountain-blue: #2f6fb3;
    --mist-blue: #cfe7f2;
    --valley-green: #1f3a36;
    --pool-blue: #a9dcf2;
    --bottle-blue: #1f7fc4;
    --bottle-light: #7fd0f4;
  }
  html, body {
    margin: 0;
    padding: 0;
    width: 1200px;
    height: 900px;
    overflow: hidden;
    background: var(--board-black);
  }
  .board {
    position: relative;
    width: 1200px;
    height: 900px;
    background: var(--board-black);
  }
  .board-frame {
    position: absolute;
    left: 30px;
    top: 30px;
    width: 1134px;
    height: 834px;
    border: 3px solid var(--frame-blue);
  }
  .board-frame::before,
  .board-frame::after {
    content: "";
    position: absolute;
    left: 0;
    right: 0;
    height: 3px;
    background: linear-gradient(90deg, var(--frame-blue), #ffffff 50%, var(--frame-blue));
  }
  .board-frame::before { top: -3px; }
  .board-frame::after { bottom: -3px; }

  .poster {
    position: absolute;
    left: 294px;
    top: 94px;
    width: 580px;
    height: 680px;
    border: 16px solid var(--poster-grey);
    background: var(--board-black);
    overflow: hidden;
  }
  .poster-scene {
    position: absolute;
    left: 0;
    top: 0;
    width: 580px;
    height: 536px;
    background:
      radial-gradient(ellipse 150px 110px at 290px 130px, #ffffff 0%, rgba(255,255,255,0) 100%),
      radial-gradient(ellipse 260px 200px at 290px 120px, var(--sun-yellow) 0%, rgba(255,242,122,0) 100%),
      linear-gradient(180deg,
        var(--sun-orange) 0%,
        #f9d55a 18%,
        var(--mountain-blue) 36%,
        var(--mist-blue) 45%,
        #4d86a7 55%,
        var(--valley-green) 70%,
        #2a4a3a 82%,
        var(--pool-blue) 94%,
        #000000 100%);
  }
  .poster-title {
    position: absolute;
    left: 0;
    width: 580px;
    margin: 0;
    text-align: center;
    font-family: "Michroma", sans-serif;
    font-weight: 400;
    color: var(--brand-red);
    letter-spacing: 1px;
  }
  .poster-title--top {
    top: 74px;
    font-size: 44px;
  }
  .poster-title--bottom {
    top: 552px;
    font-size: 56px;
  }

  .bottle {
    position: absolute;
    top: 362px;
    width: 90px;
    height: 270px;
    border-radius: 30px 30px 36px 36px;
    background: linear-gradient(90deg, var(--bottle-blue), var(--bottle-light) 45%, var(--bottle-blue));
  }
  .bottle--left { left: 76px; }
  .bottle--right { left: 1030px; }
  .splash {
    position: absolute;
    top: 600px;
    width: 200px;
    height: 70px;
    border-radius: 50%;
    background: radial-gradient(ellipse at center, rgba(127,208,244,0.8) 0%, rgba(31,127,196,0.3) 50%, rgba(0,0,0,0) 75%);
  }
  .splash--left { left: 60px; }
  .splash--right { left: 935px; }
</style>
</head>
<body>
  <main class="board">
    <div class="board-frame"></div>

    <div class="splash splash--left" role="img" aria-label="Water splash at the base of the bottle"></div>
    <div class="bottle bottle--left" role="img" aria-label="Blue Quelvane Water bottle"></div>

    <section class="poster">
      <div class="poster-scene" role="img" aria-label="Illustration of sun rays over Jamaica's Blue Mountains with waterfalls, farm fields and a spring fountain pouring into a pool"></div>
      <h1 class="poster-title poster-title--top">QUELVANE</h1>
      <p class="poster-title poster-title--bottom">QUELVANE</p>
    </section>

    <div class="splash splash--right" role="img" aria-label="Water splash at the base of the bottle"></div>
    <div class="bottle bottle--right" role="img" aria-label="Blue Quelvane Water bottle"></div>
  </main>
</body>
</html>
```